Sports hypnotherapist needs electronic letterhead design

Need a simple but classy design for a letterhead that looks good when printed. Its for a hypnotherapist who specialises in elite sport. Should have my company name and address and website details on it. I specialise in footballers.
Should look good electronically and when printed.
Include all contact details as shown in the must haves.

Target Market(s)

Sports people, elite sport.

Industry/Entity Type

Hypnotherapy

Font styles to use
Sans Serif

Colors

Designer to choose colors to be used in the design.

Requirements
Must have
• NEEDS TO BE DESIGNED IN MS WORD
• Logo +
• Calm Summit Hypnotherapists
• 27 Marlow Rise
• Bracknell
• SN7 4LT
• Tel: 07815 264731
• E: calmsummitcoaching@examplemail.co.uk
• www: http://www.calm-summit.co.uk.
• Derek Moss
• Clinical hypnotherapist, hypnoanalyst, mental resilience coach, MSc, Dip PHH
Nice to have
• A watermark?
• Plenty of space for the A4 letter
• Prints well.
Should not have
• Too much clutter.
• Too much colour that will be costly to print.

```html
<!DOCTYPE html>
<html lang="en">
<head>
<meta charset="utf-8">
<title>Calm Summit Hypnotherapists – Letterhead</title>
<link href="https://fonts.googleapis.com/css2?family=Open+Sans:wght@400;600;700&family=Fira+Sans:wght@600&display=swap" rel="stylesheet">
<style>
  :root {
    --paper: #fafafa;
    --ink: #1d1d1d;
    --body: #5a5a5a;
    --sky: #58b6e8;
    --navy: #1f2a7a;
    --white: #ffffff;
  }
  * { margin: 0; padding: 0; box-sizing: border-box; }
  html, body { width: 1102px; height: 1200px; overflow: hidden; background: var(--paper); }
  .letterhead {
    position: relative; width: 1102px; height: 1200px; overflow: hidden;
    background: var(--paper); font-family: "Open Sans", sans-serif; color: var(--body);
  }
  .watermark {
    position: absolute; left: 40px; top: 640px; width: 560px; height: 560px;
    background: linear-gradient(110deg, rgba(190,190,190,0.28) 0%, rgba(190,190,190,0.22) 45%, rgba(185,220,242,0.32) 60%, rgba(185,220,242,0.18) 100%);
    border-radius: 180px 200px 0 0;
  }
  .brand { position: absolute; left: 85px; top: 68px; display: flex; align-items: center; gap: 14px; }
  .brand-dot { width: 22px; height: 22px; border-radius: 50%; background: var(--sky); }
  .brand-name { font-size: 40px; font-weight: 700; color: var(--ink); letter-spacing: -0.5px; }
  .letter-body { position: absolute; left: 85px; top: 262px; width: 932px; font-size: 15px; line-height: 24px; }
  .salutation { padding-left: 36px; margin-bottom: 34px; }
  .letter-body p.para { text-indent: 36px; text-align: justify; margin-bottom: 18px; }
  .sign-off { position: absolute; left: 121px; top: 820px; }
  .sign-label { font-size: 14px; font-weight: 600; color: var(--body); }
  .signature { display: block; width: 220px; height: 44px; margin: 10px 0 12px -4px; border-radius: 6px; background: rgba(31,42,122,0.12); }
  .sign-role { font-size: 14px; }
  .practitioner { position: absolute; left: 85px; top: 948px; }
  .practitioner-name { font-family: "Fira Sans", sans-serif; font-weight: 600; font-size: 21px; color: var(--sky); }
  .practitioner-creds { font-size: 12.5px; line-height: 16px; color: var(--ink); margin-top: 6px; }
  .footer-wave { position: absolute; left: 0; bottom: 0; width: 1102px; height: 300px; }
  .contact { position: absolute; right: 85px; bottom: 24px; list-style: none; text-align: right; }
  .contact li { display: flex; justify-content: flex-end; align-items: center; gap: 14px; color: var(--white); font-size: 15.5px; line-height: 22px; }
  .contact svg { width: 15px; height: 15px; fill: var(--white); }
</style>
</head>
<body>
<main class="letterhead">
  <div class="watermark" role="img" aria-label="Faint watermark of a standing coach and a sprinting athlete"></div>

  <header class="brand">
    <span class="brand-dot"></span>
    <span class="brand-name">Calm Summit</span>
  </header>

  <section class="letter-body">
    <p class="salutation">Dear Sir,</p>
    <p class="para">Lorem Ipsum is simply dummy text of the printing and typesetting industry. Lorem Ipsum has been the industry's standard dummy text ever since the 1500s, when an unknown printer took a galley of type and scrambled it to make a type specimen book. It has survived not only five centuries, but also the leap into electronic typesetting, remaining essentially unchanged. It was popularised in the 1960s with the release of Quillsheet sheets containing Lorem Ipsum passages, and more recently with desktop publishing software like Pressline Composer including versions of Lorem Ipsum.</p>
    <p class="para">Lorem Ipsum is simply dummy text of the printing and typesetting industry. Lorem Ipsum has been the industry's standard dummy text ever since the 1500s, when an unknown printer took a galley of type and scrambled it to make a type specimen book. It has survived not only five centuries, but also the leap into electronic typesetting, remaining essentially unchanged. It was popularised in the 1960s with the release of Quillsheet sheets containing Lorem Ipsum passages, and more recently with desktop publishing software like Pressline Composer including versions of Lorem Ipsum.</p>
    <p class="para">Lorem Ipsum is simply dummy text of the printing and typesetting industry. Lorem Ipsum has been the industry's standard dummy text ever since the 1500s, when an unknown printer took a galley of type and scrambled it to make a type specimen book. It was popularised in the 1960s with the release of Quillsheet sheets containing Lorem Ipsum passages, and more recently with desktop publishing software like Pressline Composer including versions of Lorem Ipsum.</p>
    <p class="para">It was popularised in the 1960s with the release of Quillsheet sheets containing Lorem Ipsum passages, and more recently with desktop publishing software like Pressline Composer including versions of Lorem Ipsum.</p>
  </section>

  <section class="sign-off">
    <p class="sign-label">Your Name</p>
    <span class="signature" role="img" aria-label="Handwritten signature of Owen Thrale"></span>
    <p class="sign-role">CEO &nbsp;|&nbsp; Owner</p>
  </section>

  <section class="practitioner">
    <p class="practitioner-name">Derek Moss</p>
    <p class="practitioner-creds">Clinical Hypnotherapist,<br>Hypnoanalyst, Mental<br>Resilience Coach, Msc, Dip Phh</p>
  </section>

  <svg class="footer-wave" viewBox="0 0 1102 300" preserveAspectRatio="none" aria-hidden="true">
    <path d="M0,135 C170,215 380,250 540,215 C680,180 780,80 900,62 C980,50 1050,48 1102,48 L1102,300 L0,300 Z" fill="#1d1d1d"/>
    <path d="M0,160 C180,240 380,268 540,235 C680,202 780,104 900,84 C980,72 1050,70 1102,70 L1102,300 L0,300 Z" fill="#fafafa"/>
    <path d="M0,180 C180,262 380,290 540,255 C680,222 780,124 900,104 C980,92 1050,90 1102,90 L1102,300 L0,300 Z" fill="#58b6e8"/>
  </svg>

  <ul class="contact">
    <li>07815 264731
      <svg viewBox="0 0 16 16"><path d="M3 2h3l1.5 3.5-2 1.3a9 9 0 0 0 3.7 3.7l1.3-2L14 10v3a1.5 1.5 0 0 1-1.5 1.5A11.5 11.5 0 0 1 1.5 3.5 1.5 1.5 0 0 1 3 2z"/></svg></li>
    <li>www.calm-summit.co.uk
      <svg viewBox="0 0 16 16"><path d="M8 1a7 7 0 1 0 0 14A7 7 0 0 0 8 1zm0 1.5c.9 0 1.9 1.6 2.2 4H5.8C6.1 4.1 7.1 2.5 8 2.5zm-3.7 4H2.6a5.5 5.5 0 0 1 3-3.6 8 8 0 0 0-1.3 3.6zm7.4 0a8 8 0 0 0-1.3-3.6 5.5 5.5 0 0 1 3 3.6zM2.6 9.5h1.7a8 8 0 0 0 1.3 3.6 5.5 5.5 0 0 1-3-3.6zm3.2 0h4.4c-.3 2.4-1.3 4-2.2 4s-1.9-1.6-2.2-4zm5.9 0h1.7a5.5 5.5 0 0 1-3 3.6 8 8 0 0 0 1.3-3.6z"/></svg></li>
    <li>calmsummitcoaching@examplemail.co.uk
      <svg viewBox="0 0 16 16"><path d="M1 3.5h14v9H1zm1.4 1L8 8.6l5.6-4.1z"/></svg></li>
    <li>27 Marlow Rise Bracknell SN7 4LT
      <svg viewBox="0 0 16 16"><path d="M8 1a5 5 0 0 0-5 5c0 3.8 5 9 5 9s5-5.2 5-9a5 5 0 0 0-5-5zm0 7a2 2 0 1 1 0-4 2 2 0 0 1 0 4z"/></svg></li>
  </ul>
</main>
</body>
</html>
```